Frostvale Harborline LLC

we need a business card design

Industry/Entity Type

hvac

Contact Information for Business Card

my logo

Requirements
Must have
• my logo and same colors

```html
<!DOCTYPE html>
<html lang="en">
<head>
<meta charset="utf-8">
<title>Frostvale Harborline LLC – Business Card</title>
<link rel="stylesheet" href="https://fonts.googleapis.com/css2?family=Montserrat:wght@400;500;700;800&display=swap">
<style>
  :root {
    --stage: #b3b3b3;
    --brand-blue: #0b5ea8;
    --deep-blue: #0a4f8f;
    --accent-gold: #f2b33d;
    --paper: #ffffff;
    --ink: #1f1f1f;
  }
  * { margin: 0; padding: 0; box-sizing: border-box; }
  html, body { width: 1200px; height: 900px; overflow: hidden; }
  body {
    background: var(--stage);
    font-family: "Montserrat", Arial, sans-serif;
    position: relative;
  }
  .card {
    position: absolute;
    border-bottom: 5px solid var(--accent-gold);
    border-right: 5px solid var(--accent-gold);
    overflow: hidden;
  }
  /* Front: portrait */
  .card-front {
    left: 70px; top: 150px;
    width: 340px; height: 595px;
    background: var(--paper);
  }
  .front-band {
    height: 270px;
    background: var(--brand-blue);
    display: flex; align-items: center; justify-content: center;
    gap: 10px; padding: 0 22px;
  }
  .brand-dot {
    width: 18px; height: 18px; border-radius: 50%;
    background: var(--accent-gold); flex: none;
  }
  .brand-name {
    color: var(--paper);
    font-weight: 800;
    font-size: 25px;
    line-height: 1.15;
    text-transform: uppercase;
    letter-spacing: 0.5px;
  }
  .front-body { padding: 34px 28px 0; }
  .person-name {
    color: var(--brand-blue);
    font-weight: 700; font-size: 26px;
  }
  .person-title {
    color: var(--ink); font-size: 14px; margin-top: 4px;
  }
  .address {
    margin-top: 70px;
    font-size: 14px; line-height: 1.45; color: var(--ink);
  }
  .contact-list { list-style: none; margin-top: 14px; }
  .contact-list li {
    display: flex; align-items: center; gap: 12px;
    font-size: 14px; line-height: 1.9; color: var(--ink);
  }
  .contact-list svg { width: 15px; height: 15px; flex: none; }
  /* Back: landscape */
  .card-back {
    left: 470px; top: 255px;
    width: 680px; height: 390px;
    background: var(--brand-blue);
    display: flex; align-items: center; justify-content: center;
  }
  .back-pattern {
    position: absolute; inset: 0;
    background: linear-gradient(135deg, var(--brand-blue), var(--deep-blue));
  }
  .back-brand {
    position: relative;
    display: flex; align-items: center; gap: 16px;
  }
  .back-brand .brand-dot { width: 26px; height: 26px; }
  .back-brand .brand-name { font-size: 38px; }
</style>
</head>
<body>

<section class="card card-front" aria-label="Business card front">
  <div class="front-band">
    <span class="brand-dot"></span>
    <span class="brand-name">Frostvale Harborline LLC</span>
  </div>
  <div class="front-body">
    <h1 class="person-name">Dorian Vale</h1>
    <p class="person-title">Managing Director</p>
    <p class="address">48 Quay Lane,<br>Marlow, FL 33610</p>
    <ul class="contact-list">
      <li>
        <svg viewBox="0 0 16 16" aria-hidden="true"><rect x="3" y="1" width="10" height="14" rx="2" fill="none" stroke="#f2b33d" stroke-width="1.8"/></svg>
        +1 (555) 014-2290
      </li>
      <li>
        <svg viewBox="0 0 16 16" aria-hidden="true"><rect x="1" y="3" width="14" height="10" rx="1" fill="#f2b33d"/><path d="M1 4l7 5 7-5" fill="none" stroke="#fff" stroke-width="1.3"/></svg>
        hello@frostvalehvac.com
      </li>
      <li>
        <svg viewBox="0 0 16 16" aria-hidden="true"><circle cx="8" cy="8" r="7" fill="#f2b33d"/><path d="M1 8h14M8 1c-3 4-3 10 0 14M8 1c3 4 3 10 0 14" fill="none" stroke="#fff" stroke-width="1.1"/></svg>
        www.frostvalehvac.com
      </li>
    </ul>
  </div>
</section>

<section class="card card-back" aria-label="Business card back">
  <div class="back-pattern" role="img" aria-label="Faint repeating brand pattern on blue"></div>
  <div class="back-brand">
    <span class="brand-dot"></span>
    <span class="brand-name">Frostvale Harborline LLC</span>
  </div>
</section>

</body>
</html>
```